Hop Bright Meadow Business Website Branding

Looking for a wordpress template design with CSS and HTML encoding. Current website can be seen at hopbrightmeadow.example.

WE ARE CURRENTLY IN PROCESS GETTING A LOGO DESIGN... I HAVE INCLUDED THE TOP POTENTIAL DESIGNS FOR REFERENCE TO HELP UNDERSTAND WHAT STYLE WE ARE LOOKING FOR...
NOTE: THE “PEBBLE CREW” LOGO WAS A PREVIOUS COMPANY WE OWNED SO YOU CAN GE A FEEL FOR THE TYPE OF DESIGNS WE HAVE USED IN THE PAST.

My blog will focus on making a connection with wild Florida, it’s wildlife, plants and animals... with an eye toward Florida conservation, nature adventure trips, and education... Content, photos and other merchandise will also be offered for sale.
I’m looking for a site design that incorporates Florida nature and wildlife/plants, with a fun “Old Florida” retro-adventure feel.
When they see this site it should speak to the import of natural Florida and the critical nature of the ecosystem here... while being instantly recognizable and iconic... IE: when I think of florida I think of water, plants, warmth, sunsets etc...

https://join.chatroomhub.example/t/lumexstudio-kzt4821/shared_invite/zt-pqwrt83m-hRnLvXaKoPzsYcB1Uq7JdM

Target Market(s)

Nature, Education, Conservation, Photography

Industry/Entity Type

Photographer

Coding

Coded - Design and coding required

Requirements
Must have
• Need to have site wide template design which generally includes a landing page and a general page template for other pages... Must include html and css encoding...
Should not have
• Any animals included in the site should be Florida native... IE: no African animals etc... This will require some research to ensure that if animals are included that they are part of the Florida ecosystem.

```html
<!DOCTYPE html>
<html lang="en">
<head>
<meta charset="utf-8">
<title>Hop Bright Meadow</title>
<link rel="stylesheet" href="https://fonts.googleapis.com/css2?family=Poppins:wght@400;500;600;700&family=Tinos:wght@400;700&family=Roboto+Condensed:wght@700&family=Lato:wght@400;700&display=swap">
<style>
:root{
  --green:#3f9d1c;
  --green-bright:#4fbf3a;
  --green-deep:#2f8a12;
  --ink:#1f1f1f;
  --muted:#555;
  --cream:#f5f3ee;
  --footer:#1e261f;
  --footer-line:#2a332b;
  --red:#e0261b;
  --gold:#e8a21a;
  --white:#fff;
}
*{box-sizing:border-box;margin:0;padding:0}
html,body{width:1200px;height:3173px;overflow:hidden;background:#fff}
body{font-family:"Tinos",serif;color:var(--ink);position:relative}
.abs{position:absolute}

/* admin bar */
.admin-bar{position:absolute;left:0;top:0;width:1200px;height:20px;background:#23282d;color:#eee;font:400 9px "Lato",sans-serif;display:flex;align-items:center;padding:0 10px;gap:16px}
.admin-bar .right{margin-left:auto}

/* hero */
.hero{position:absolute;left:0;top:20px;width:1200px;height:505px;overflow:hidden;
  background:radial-gradient(ellipse 300px 220px at 1000px 40px,rgba(255,245,200,.55),transparent 70%),
  radial-gradient(ellipse 700px 260px at 1000px 520px,#6f9a2e,transparent 70%),
  linear-gradient(180deg,#3b4140 0%,#4e5550 45%,#5a5442 75%,#4a4436 100%)}
.hero .tree{position:absolute;left:640px;top:0;width:300px;height:380px;background:radial-gradient(ellipse 150px 120px at 150px 90px,rgba(40,60,25,.75),transparent 75%)}
.brand{position:absolute;left:222px;top:26px;font:600 14px "Poppins",sans-serif;color:var(--green-bright);display:flex;align-items:center;gap:7px}
.brand i{width:10px;height:10px;border-radius:50%;background:var(--green-bright);display:block}
.nav{position:absolute;left:509px;top:27px;display:flex;gap:21px;font:400 11px "Tinos",serif;color:#e8e8e8}
.nav .on{color:#fff}
.phone{position:absolute;left:860px;top:24px;font:500 15px "Poppins",sans-serif;color:var(--green-bright)}
.eyebrow{position:absolute;left:240px;top:136px;font:600 7.5px "Poppins",sans-serif;letter-spacing:1.2px;color:var(--green-bright)}
.eyebrow-rule{position:absolute;left:240px;top:156px;width:20px;height:2px;background:var(--green-bright)}
.hero h1{position:absolute;left:240px;top:170px;font:600 41px/1.08 "Poppins",sans-serif;color:#fff}
.hero p{position:absolute;left:600px;top:176px;width:312px;font:400 11px/18px "Tinos",serif;color:#f2f2f2}
.btn{display:inline-flex;align-items:center;justify-content:center;gap:10px;background:var(--green);color:#fff;font:600 10px "Poppins",sans-serif}
.hero .btn{position:absolute;left:600px;top:310px;width:103px;height:30px;border-radius:3px;background:#3da538}
.socials{position:absolute;left:240px;top:476px;display:flex;gap:22px}
.socials span{width:10px;height:10px;border-radius:50%;background:#fff;display:block}
.hero .addr{position:absolute;left:600px;top:473px;font:400 10.5px "Tinos",serif;color:#fff;display:flex;gap:7px;align-items:center}

/* produce */
.section-title{font:600 25px "Poppins",sans-serif;text-align:center;color:var(--ink)}
.produce-title{position:absolute;left:0;top:558px;width:1200px}
.produce-sub{position:absolute;left:0;top:605px;width:1200px;text-align:center;font:400 11px "Lato",sans-serif;color:#222}
.produce-grid{position:absolute;left:253px;top:639px;display:grid;grid-template-columns:repeat(3,223px);grid-template-rows:repeat(2,154px);column-gap:12px;row-gap:26px}
.tile{position:relative;overflow:hidden}
.tile .photo{position:absolute;inset:0}
.tile .label{position:absolute;left:0;right:0;bottom:0;height:34px;background:rgba(30,30,30,.45);display:flex;align-items:center;gap:10px;padding-left:3px;font:700 13px "Roboto Condensed",sans-serif;color:#fff;letter-spacing:-.3px}

/* stop polluters */
.polluters h2{position:absolute;left:247px;top:1068px;font:600 25px "Poppins",sans-serif}
.polluters p{position:absolute;left:247px;top:1110px;width:320px;font:400 11px/21px "Lato",sans-serif;color:#555}
.polluters .btn{position:absolute;left:247px;top:1218px;width:88px;height:29px;font-size:9.5px;background:var(--green-deep)}
.leaf{position:absolute;left:583px;top:1069px;width:370px;height:208px;border-radius:260px 0 260px 0/208px 0 208px 0;background:radial-gradient(ellipse 120px 80px at 240px 60px,#b68a6a,transparent 70%),linear-gradient(180deg,#7dac2a 0%,#4f7b18 55%,#3a2a1a 85%,#2a1d12 100%)}
.play{position:absolute;left:738px;top:1143px;width:60px;height:60px;border-radius:50%;border:3px solid rgba(255,255,255,.85)}

/* events */
.events-title{position:absolute;left:0;top:1353px;width:1200px;font:600 24px "Poppins",sans-serif;text-align:center}
.trees{position:absolute;left:564px;top:1404px}
.events-sub{position:absolute;left:0;top:1441px;width:1200px;text-align:center;font:400 10px "Lato",sans-serif}
.events-box{position:absolute;left:240px;top:1472px;width:719px;height:358px;background:var(--cream);display:flex;gap:13px;padding:6px}
.event{width:226px}
.event .photo{height:176px;position:relative}
.event .date{position:absolute;left:65px;top:76px;width:97px;height:27px;background:var(--green-deep);color:#fff;font:400 11px "Tinos",serif;display:flex;align-items:center;justify-content:center}
.event h3{font:500 14px/16px "Poppins",sans-serif;text-transform:uppercase;margin:20px 0 0 6px;color:#222}
.event p{font:400 11px/12px "Lato",sans-serif;color:#333;margin:12px 6px 0 6px;height:52px}
.event .meta{margin:0 0 0 6px;font:400 10.5px "Tinos",serif;color:#444;display:flex;flex-direction:column;gap:6px}
.event .meta span{display:flex;align-items:center;gap:6px}
.load{position:absolute;left:529px;top:1867px;width:142px;height:31px;background:#2fa31a;font-size:10.5px}

/* about */
.about{position:absolute;left:0;top:1953px;width:1200px;height:261px;background:var(--cream)}
.avatar{position:absolute;left:240px;top:65px;width:124px;height:124px;border-radius:50%;background:radial-gradient(circle at 50% 40%,#c98a5c,#4a88a8 75%)}
.about p{position:absolute;left:405px;top:64px;width:554px;font:400 10.6px/15.2px "Tinos",serif;color:#666;text-align:justify}
.about p b{color:var(--red);font-weight:400}

/* photography */
.photo-title{position:absolute;left:0;top:2237px;width:1200px;text-align:center;font:500 19px "Poppins",sans-serif;color:#333}
.photo-title b{color:var(--red);font-weight:500}
.gallery{position:absolute;left:247px;top:2293px;display:flex;gap:8px}
.gallery div{width:230px;height:203px}
.arrow-nav{position:absolute;top:2384px;color:#fff;font:400 18px "Lato",sans-serif}

/* news / quote */
.news-title{position:absolute;left:0;top:2556px;width:1200px;text-align:center;font:500 18px "Poppins",sans-serif;color:#333}
.quote{position:absolute;left:0;top:2603px;width:1200px;height:245px;background:radial-gradient(ellipse 260px 140px at 600px 160px,rgba(214,150,60,.7),transparent 70%),linear-gradient(180deg,#2b2e26,#3b3a2c 55%,#4a4230)}
.quote .rule{position:absolute;left:590px;top:88px;width:20px;height:2px;background:var(--green-bright)}
.quote blockquote{position:absolute;left:0;top:96px;width:1200px;text-align:center;font:600 18px/19.5px "Poppins",sans-serif;color:#fff}
.quote cite{position:absolute;left:0;top:166px;width:1200px;text-align:center;font:500 12px "Poppins",sans-serif;color:var(--gold);font-style:normal}

/* footer */
.footer{position:absolute;left:0;top:2848px;width:1200px;height:325px;background:var(--footer);color:#c9ccc8}
.footer .logo{position:absolute;left:240px;top:70px;font:600 25px "Poppins",sans-serif;color:#fff}
.footer h4{font:500 15px "Poppins",sans-serif;color:#fff}
.footer .frule{width:20px;height:2px;background:var(--green-bright);margin-top:10px}
.fcontact{position:absolute;left:240px;top:116px;font:400 9.5px/16px "Tinos",serif;display:flex;flex-direction:column;gap:4px}
.fcontact span{display:flex;gap:10px;align-items:flex-start}
.fcontact a{color:#fff;font:600 9.5px "Poppins",sans-serif;text-decoration:none;border-bottom:1px solid #fff;padding-bottom:2px;align-self:flex-start;margin-top:6px}
.fcol2{position:absolute;left:492px;top:72px;width:190px}
.fcol2 p{font:400 9.5px/16px "Tinos",serif;margin-top:14px}
.fsoc{display:flex;gap:11px;margin-top:24px}
.fsoc span{width:25px;height:25px;border-radius:50%;background:#37443a;display:flex;align-items:center;justify-content:center}
.fsoc span i{width:7px;height:7px;border-radius:50%;background:var(--green-bright)}
.fcol3{position:absolute;left:743px;top:72px;width:220px}
.flinks{display:grid;grid-template-columns:105px 105px;row-gap:6px;margin-top:14px;font:400 9.5px/13px "Tinos",serif}
.copy{position:absolute;left:240px;top:299px;font:400 9px "Tinos",serif;color:#bbb}
</style>
</head>
<body>

<div class="admin-bar"><span>Verdanta</span><span>Customize</span><span>1</span><span>0</span><span>+ New</span><span>Edit Page</span><span>Edit with Page Builder</span><span>Form Kit</span><span class="right">Howdy, admin</span></div>

<header class="hero">
  <div class="tree" role="img" aria-label="Lone tree on cracked earth turning to green grass under a cloudy sky"></div>
  <div class="brand"><i></i>Hop Bright Meadow</div>
  <nav class="nav"><span class="on">Home</span><span>My Blogs</span><span>Our Product</span><span>Our Album</span><span>Contact Us</span></nav>
  <div class="phone">555 014 2290</div>
  <div class="eyebrow">EXPLORING FLORIDA'S NATURAL WONDERS</div>
  <div class="eyebrow-rule"></div>
  <h1>Hop Bright<br>Meadow!</h1>
  <p>Come explore wild places and stunning scenery with me as I discover new and exciting eco-adventures and learn about the rare and unique wildlife and environments that make Florida so precious and extraordinary. I hope you can vicariously enjoy the wild and untamed beauty of Florida through my eyes, and learn some amazing things about nature on our explorations.</p>
  <a class="btn">Learn More <svg width="5" height="7" viewBox="0 0 5 7"><path d="M0 0l5 3.5L0 7z" fill="#fff"/></svg></a>
  <div class="socials"><span></span><span></span><span></span><span></span></div>
  <div class="addr"><svg width="8" height="11" viewBox="0 0 8 11"><path d="M4 0a4 4 0 0 0-4 4c0 3 4 7 4 7s4-4 4-7a4 4 0 0 0-4-4zm0 5.5a1.5 1.5 0 1 1 0-3 1.5 1.5 0 0 1 0 3z" fill="#4fbf3a"/></svg>4120 Fernhollow Rd, Cedarvale, CA 90417, USA</div>
</header>

<section class="produce">
  <h2 class="section-title produce-title">Our Produce</h2>
  <div class="produce-sub">WE ARE CONCERNING ABOUT FOLLOWING ISSUES AND OUR MISSIONS ARE SOLVING THOSE ACROSS GLOBE.</div>
  <div class="produce-grid">
    <div class="tile"><div class="photo" role="img" aria-label="Stacked cut tree logs" style="background:linear-gradient(135deg,#6b6258,#3e3832)"></div><div class="label">STOP CUTTING DOWN TREES <svg width="18" height="16" viewBox="0 0 18 16"><path d="M1 8h14M9 2l6 6-6 6" stroke="#fff" stroke-width="2.5" fill="none"/></svg></div></div>
    <div class="tile"><div class="photo" role="img" aria-label="Glowing light bulb" style="background:radial-gradient(circle at 40% 55%,#e88a2a,#3a3a3a 55%,#2a2a2a)"></div><div class="label">&nbsp;BE EFFICIENT IN ENERGY USE <svg width="18" height="16" viewBox="0 0 18 16"><path d="M1 8h14M9 2l6 6-6 6" stroke="#fff" stroke-width="2.5" fill="none"/></svg></div></div>
    <div class="tile"><div class="photo" role="img" aria-label="Smoke rising behind pine trees" style="background:linear-gradient(180deg,#7aa7d8,#a9b8c0 50%,#3e5a2a)"></div><div class="label">&nbsp;REDUCING GREENHOUSE GAS <svg width="18" height="16" viewBox="0 0 18 16"><path d="M1 8h14M9 2l6 6-6 6" stroke="#fff" stroke-width="2.5" fill="none"/></svg></div></div>
    <div class="tile"><div class="photo" role="img" aria-label="Desert tree under blue sky" style="background:linear-gradient(180deg,#2f72c4,#a8c8e6 55%,#8a7a5a)"></div><div class="label">PREVENTING AIR POLLUTION <svg width="18" height="16" viewBox="0 0 18 16"><path d="M1 8h14M9 2l6 6-6 6" stroke="#fff" stroke-width="2.5" fill="none"/></svg></div></div>
    <div class="tile"><div class="photo" role="img" aria-label="Green waste bin on pavement" style="background:radial-gradient(ellipse 50px 70px at 50% 45%,#5fae2a,#5a5048 70%)"></div><div class="label">&nbsp;RECYCLING THE DAILY WASTE <svg width="18" height="16" viewBox="0 0 18 16"><path d="M1 8h14M9 2l6 6-6 6" stroke="#fff" stroke-width="2.5" fill="none"/></svg></div></div>
    <div class="tile"><div class="photo" role="img" aria-label="Kitchen tap running into a sink" style="background:linear-gradient(135deg,#d8d8d4,#7a7874 60%,#3a3834)"></div><div class="label">&nbsp;&nbsp;BEING WATER WISE AT HOME <svg width="18" height="16" viewBox="0 0 18 16"><path d="M1 8h14M9 2l6 6-6 6" stroke="#fff" stroke-width="2.5" fill="none"/></svg></div></div>
  </div>
</section>

<section class="polluters">
  <h2>STOP POLLUTERS</h2>
  <p>Polluters must quit debilitating the privileges of defense less groups and undermining atmosphere science and activity. Give an application directly to the local mayor and we will be forwarding it.</p>
  <a class="btn">Take Action</a>
  <div class="leaf" role="img" aria-label="Hand pouring water onto a young seedling"></div>
  <svg class="play" viewBox="0 0 60 60" style="border:none"><circle cx="30" cy="30" r="27" stroke="rgba(255,255,255,.85)" stroke-width="3" fill="none"/><path d="M25 20l14 10-14 10z" fill="rgba(255,255,255,.85)"/></svg>
</section>

<section class="events">
  <h2 class="events-title">UPCOMING EVENTS</h2>
  <svg class="trees" width="72" height="14" viewBox="0 0 72 14"><g fill="#3f9d1c"><path d="M4 0l4 7H6l2 4H5v3H3v-3H0l2-4H0z"/><path d="M15 0l4 7h-2l2 4h-3v3h-2v-3h-3l2-4h-2z"/><path d="M26 0l4 7h-2l2 4h-3v3h-2v-3h-3l2-4h-2z"/><path d="M37 0l4 7h-2l2 4h-3v3h-2v-3h-3l2-4h-2z"/><path d="M48 0l4 7h-2l2 4h-3v3h-2v-3h-3l2-4h-2z"/><path d="M59 0l4 7h-2l2 4h-3v3h-2v-3h-3l2-4h-2z"/></g></svg>
  <div class="events-sub">CLIMATE ARE CHANGING BY NATURAL AND HUMAN ACTIVITIES AND WE ARE GROWING AWARENESS IN MANY COUNTRIES.</div>
  <div class="events-box">
    <article class="event">
      <div class="photo" role="img" aria-label="Rocket launch with orange smoke clouds" style="background:radial-gradient(ellipse 90px 60px at 50% 60%,#f08a2a,#6a6258 70%,#3a3a3a)"><div class="date">22 JULY 2017</div></div>
      <h3>Developing Low Carbon</h3>
      <p>We should research and develop more efficient carbon technologies to protect against global warming around the world.</p>
      <div class="meta"><span><svg width="8" height="8" viewBox="0 0 8 8"><circle cx="4" cy="4" r="4" fill="#444"/><path d="M4 1.5V4h2" stroke="#fff" fill="none"/></svg>02:00pm - 04:00pm</span><span><svg width="9" height="9" viewBox="0 0 9 9"><path d="M9 0L0 4l4 1 1 4z" fill="#444"/></svg>Marrow Flats, Texas</span></div>
    </article>
    <article class="event">
      <div class="photo" role="img" aria-label="City plaza with green lawns and tall buildings" style="background:linear-gradient(180deg,#8a8f98,#6a7a6a 55%,#5f8a4a)"><div class="date">22 JULY 2017</div></div>
      <h3>Encouraging To A Green City</h3>
      <p>Growing awareness about greenhouse among the people and full encourages them to clean the city for our healthy life.</p>
      <div class="meta"><span><svg width="8" height="8" viewBox="0 0 8 8"><circle cx="4" cy="4" r="4" fill="#444"/><path d="M4 1.5V4h2" stroke="#fff" fill="none"/></svg>02:00pm - 04:00pm</span><span><svg width="9" height="9" viewBox="0 0 9 9"><path d="M9 0L0 4l4 1 1 4z" fill="#444"/></svg>Marrow Flats, Texas</span></div>
    </article>
    <article class="event">
      <div class="photo" role="img" aria-label="Snowy mountain peaks above clouds" style="background:linear-gradient(180deg,#b8c4cc,#e8eaec 55%,#8a8e90)"><div class="date">22 JULY 2017</div></div>
      <h3>Prevent Warm In Antarctica</h3>
      <p>Ice is melting in Antarctica by natural and human activities. As a result, water increased the risk of sea-level rise.</p>
      <div class="meta"><span><svg width="8" height="8" viewBox="0 0 8 8"><circle cx="4" cy="4" r="4" fill="#444"/><path d="M4 1.5V4h2" stroke="#fff" fill="none"/></svg>02:00pm - 04:00pm</span><span><svg width="9" height="9" viewBox="0 0 9 9"><path d="M9 0L0 4l4 1 1 4z" fill="#444"/></svg>Marrow Flats, Texas</span></div>
    </article>
  </div>
  <a class="btn load">- Load All Events -</a>
</section>

<section class="about">
  <div class="avatar" role="img" aria-label="Portrait of the site author by the sea"></div>
  <p>Hello nature lovers! I'm <b>Marisol Tenbrook</b>, a wildlife educator, Florida Master Naturalist, nature writer and photographer, busy mama of three kiddos, a playful Havanese puppy, two very chubby guinea pigs, and a giant tree frog. I have a passion for all things nature and I adore living in Southwest Florida. I will always be a California girl, but from the moment I set foot in Florida, its wild beauty stole my heart. For the past 23 years, I have been fortunate to have some very unique and special experiences caring for many different species of animals and educating the public about wildlife and the environment. My hope is that those I endeavor to educate will better understand their connection with the natural world and our shared responsibility to protect Florida's wild and priceless beauty.</p>
</section>

<section class="photography">
  <h2 class="photo-title">All Photography By <b>Marisol Tenbrook</b></h2>
  <div class="gallery">
    <div role="img" aria-label="Yellow wildflowers among green leaves" style="background:radial-gradient(circle at 45% 45%,#e8b020,#4a6a2a 60%,#2e4a1e)"></div>
    <div role="img" aria-label="White wildflowers in a pine woodland" style="background:linear-gradient(180deg,#5a6a4a,#6a8a4a 60%,#4a5a34)"></div>
    <div role="img" aria-label="Orange lily flower close-up" style="background:radial-gradient(circle at 55% 50%,#f4c040,#ee5a2a 45%,#e0401a)"></div>
  </div>
  <span class="arrow-nav" style="left:256px">&#8249;</span>
  <span class="arrow-nav" style="left:933px">&#8250;</span>
</section>

<h2 class="news-title">Latest News</h2>
<section class="quote" role="img" aria-label="Misty forest at sunset">
  <div class="rule"></div>
  <blockquote>“Nature Has Been For Me, As Long As I Remember, A<br>Source Of Solace, Inspiration, Adventure, And Delight;<br>A Home, A Teacher, A Companion.</blockquote>
  <cite>| Delia Harrowgate</cite>
</section>

<footer class="footer">
  <div class="logo">Your Logo</div>
  <div class="fcontact">
    <span><svg width="7" height="10" viewBox="0 0 8 11" style="margin-top:3px"><path d="M4 0a4 4 0 0 0-4 4c0 3 4 7 4 7s4-4 4-7a4 4 0 0 0-4-4z" fill="#4fbf3a"/></svg>4120 Fernhollow Rd, Cedarvale,<br>CA 90417, USA</span>
    <span><svg width="8" height="8" viewBox="0 0 8 8" style="margin-top:4px"><path d="M1 0l2 2-1 1.5a5 5 0 0 0 2.5 2.5L6 5l2 2-1 1C3 8 0 5 0 1z" fill="#4fbf3a"/></svg>+44 555 014 7731</span>
    <span><svg width="9" height="7" viewBox="0 0 9 7" style="margin-top:4px"><rect width="9" height="7" fill="#4fbf3a"/><path d="M0 0l4.5 4L9 0" stroke="#1e261f" fill="none"/></svg>hello@hopbrightmeadow.example</span>
    <a>Get A Direction</a>
  </div>
  <div class="fcol2">
    <h4>Get In Touch</h4><div class="frule"></div>
    <p>Send us a note about field trips, prints or talks and we will reply within two days.</p>
    <div class="fsoc"><span><i></i></span><span><i></i></span><span><i></i></span><span><i></i></span></div>
  </div>
  <div class="fcol3">
    <h4>Quick Link</h4><div class="frule"></div>
    <div class="flinks"><span>Home</span><span>Bundles</span><span>Our Farm</span><span>Consulting</span><span>Our Product</span><span>Subscriptions</span><span>Testimonial</span><span>Learn</span><span>Contact us</span><span>Community</span></div>
  </div>
  <div class="copy">Copyright © 2020</div>
</footer>

</body>
</html>
```